Business Card Design - Photographer

I am a landscape photographer and I require a business card design. 

I require two designs:
1)  a double sided business card
 and
b)  a single sided business card 

The single sided design can either be the same as the double sided (with just one side having all the information)....or it can be an entire new design. Its up to you.

My corporate colours are (CMYK):

Blue   69, 32, 0, 0
Grey  72,  64,  47,  31
Green  32,  2,  91,  0
Yellow   0, 19, 92, 0
Orange  0, 39, 75, 0

Colour space in final file should be in CMYK.

The details that need to be included on the card:

- Use the provided Logo
- Name: Wiktor Baranowski
- Email:   sales@vistalumeworks.com.au
- Website:    vistalumeworks.com.au
- Twitter:    twitter.com/vistalumeworks
- Facebook:   facebook.com/vistalumeworks
- Mobile  0417 539 662

Please use the attached template to design the logo to the specified size, including the marked bleed lines. I have also attached my logo in PNG (transparent background) and ai format for you to use.

The final file should be:
- Photoshop version with layers so I can edit the name/text etc. All non vector files should be high resolution at 1039 x 697 pixels at 300 dpi.

I also require a file as:
- Vector based PDF

Anyway questions please contact me.

Thank you

Industry/Entity Type

Landscape

Logo styles of interest
Pictorial/Combination Logo
Abstract Logo
Wordmark Logo
Lettermark Logo
Requirements
Must have
• The details that need to be included on the card:

- Use the provided Logo
- Name: Wiktor Baranowski
- Email: sales@vistalumeworks.com.au
- Website: vistalumeworks.com.au
- Twitter: twitter.com/vistalumeworks
- Facebook: facebook.com/vistalumeworks
- Mobile 0417 539 662

```html
<!DOCTYPE html>
<html lang="en">
<head>
<meta charset="utf-8">
<title>Vistalume Works — Business Cards</title>
<link rel="stylesheet" href="https://fonts.googleapis.com/css2?family=Cinzel:wght@500;600&family=Open+Sans:wght@400&display=swap">
<style>
  :root {
    --ink: #3d4251;
    --ink-soft: #5b6070;
    --brand-blue: #3a9ad9;
    --brand-green: #b5d334;
    --brand-yellow: #fdcb1f;
    --brand-orange: #f7a14a;
    --card: #ffffff;
    --backdrop: #e8e6e3;
    --mark-grey: #d5d7dc;
  }
  * { box-sizing: border-box; margin: 0; padding: 0; }
  html, body { width: 1200px; height: 758px; overflow: hidden; }
  body {
    background: var(--backdrop);
    position: relative;
    font-family: "Open Sans", Arial, sans-serif;
    color: var(--ink);
  }
  .card {
    position: absolute;
    top: 198px;
    width: 540px;
    height: 362px;
    background: var(--card);
    box-shadow: 0 6px 22px rgba(0,0,0,.18);
    overflow: hidden;
  }
  .card--front { left: 40px; }
  .card--back { left: 620px; }

  .lockup {
    position: absolute;
    display: flex;
    flex-direction: column;
    align-items: center;
  }
  .card--front .lockup { left: 50px; top: 40px; width: 320px; }
  .card--back .lockup { left: 170px; top: 92px; width: 320px; }

  .lockup__dot {
    width: 62px; height: 62px;
    border-radius: 50%;
    background: var(--ink);
    margin-bottom: 14px;
  }
  .lockup__name {
    font-family: "Cinzel", "Times New Roman", serif;
    font-weight: 600;
    font-size: 30px;
    letter-spacing: 1px;
    color: var(--ink);
    line-height: 1;
    padding-bottom: 6px;
    border-bottom: 1.5px solid var(--ink);
    white-space: nowrap;
  }
  .lockup__tagline {
    font-family: "Cinzel", "Times New Roman", serif;
    font-weight: 500;
    font-size: 11.5px;
    letter-spacing: 2.4px;
    color: var(--ink);
    margin-top: 6px;
  }

  .contacts {
    position: absolute;
    left: 50px; top: 214px; width: 320px;
    display: flex; flex-direction: column; align-items: center; gap: 7px;
    font-size: 12px;
    color: var(--ink-soft);
  }
  .contacts__row { display: flex; align-items: center; gap: 12px; white-space: nowrap; }
  .contacts__item { display: inline-flex; align-items: center; gap: 5px; }
  .icon { width: 11px; height: 11px; fill: var(--ink-soft); flex: none; }
  .social-square { width: 10px; height: 10px; background: var(--brand-blue); border-radius: 2px; flex: none; }
  .contacts__address { margin-top: 4px; font-size: 12.5px; letter-spacing: 1.4px; }

  .card--back .web {
    position: absolute;
    left: 170px; top: 232px; width: 320px;
    text-align: center;
    font-size: 12.5px;
    letter-spacing: 1.6px;
    color: var(--ink-soft);
  }
</style>
</head>
<body>
  <section class="card card--front" aria-label="Card front">
    <div class="lockup">
      <span class="lockup__dot"></span>
      <div class="lockup__name">VISTALUME WORKS</div>
      <div class="lockup__tagline">FINE ART PHOTOGRAPHY</div>
    </div>
    <div class="contacts">
      <div class="contacts__row">
        <span class="contacts__item">
          <svg class="icon" viewBox="0 0 12 12" aria-hidden="true"><rect x="3" y="0.5" width="6" height="11" rx="1.2"/><rect x="4.2" y="2" width="3.6" height="6" fill="#fff"/></svg>
          0417 539 662
        </span>
        <span class="contacts__item">
          <svg class="icon" viewBox="0 0 12 12" aria-hidden="true"><rect x="0.5" y="2.5" width="11" height="7.5" rx="0.8"/><path d="M1 3 L6 7 L11 3" stroke="#fff" stroke-width="1" fill="none"/></svg>
          sales@vistalumeworks.com.au
        </span>
      </div>
      <div class="contacts__row">
        <span class="contacts__item">
          <svg class="icon" viewBox="0 0 12 12" aria-hidden="true"><circle cx="6" cy="6" r="5.2"/><path d="M1 6h10M6 1c-2.2 2.6-2.2 7.4 0 10M6 1c2.2 2.6 2.2 7.4 0 10" stroke="#fff" stroke-width=".8" fill="none"/></svg>
          www.vistalumeworks.com.au
        </span>
      </div>
      <div class="contacts__row">
        <span class="contacts__item"><span class="social-square"></span>vistalumeworks</span>
        <span class="contacts__item"><span class="social-square"></span>vistalumeworks</span>
      </div>
      <div class="contacts__address">00, Complex name, state, city 0020</div>
    </div>
  </section>

  <section class="card card--back" aria-label="Card back">
    <div class="lockup">
      <span class="lockup__dot"></span>
      <div class="lockup__name">VISTALUME WORKS</div>
      <div class="lockup__tagline">FINE ART PHOTOGRAPHY</div>
    </div>
    <div class="web">www.vistalumeworks.com.au</div>
  </section>
</body>
</html>
```